Harvest Gateway Fellowship Ministries needs a fresh new web design

We are an up and coming multicultural church that aims to bring people into a life changing encounter with God. We need a fresh and inviting website in order to increase our internet presence and make us easier to connect with.
Here are some of the basic requirements for the site:
• Clearly displayed address, service times, and contact info
• A staff profile page
• An area for a calendar with upcoming events and their details
• Social media buttons
• Group pages for the different ministries (youth, children’s church, men, etc…)
• An area for donations and eCommerce
• A resources page for assorted media (podcasts, sermons, videos, etc.…)
• An area for prayer requests.

```html
<!DOCTYPE html>
<html lang="en">
<head>
<meta charset="utf-8">
<title>Harvest Gateway Fellowship Ministries</title>
<link rel="stylesheet" href="https://fonts.googleapis.com/css2?family=Roboto:wght@400;500;700&family=Open+Sans:wght@400;600&display=swap">
<style>
:root{
  --blue:#2f8fd2;
  --blue-dark:#1d6fb3;
  --blue-light:#55aee8;
  --sky-top:#3b4a5e;
  --sky-mid:#8fb2cf;
  --sky-low:#c9dbe8;
  --ink:#333;
  --muted:#555;
  --grey-bar:#8a8a8a;
  --cream:#f8efdc;
  --gold:#e3c269;
  --white:#fff;
  --line:#d7d7d7;
}
*{box-sizing:border-box;margin:0;padding:0}
html,body{width:927px;height:1200px;overflow:hidden}
body{position:relative;font-family:"Open Sans",sans-serif;color:var(--ink);background:var(--white)}
.abs{position:absolute}

.top-band{left:0;top:0;width:927px;height:101px;background:linear-gradient(180deg,#2b3442,#4d5b6c 70%,#6b7a8a)}
.contact-info,.service-times{top:42px;color:var(--white);font-size:8.5px;line-height:13px;display:flex;gap:8px;align-items:center}
.contact-info{left:134px}
.service-times{left:663px}

.main-nav{left:0;top:101px;width:927px;height:44px;background:linear-gradient(180deg,var(--blue-light),var(--blue))}
.nav-item{top:0;height:44px;line-height:44px;color:var(--white);font-family:"Roboto",sans-serif;font-size:11.5px;text-transform:uppercase}
.nav-item.active{background:var(--blue-dark);padding:0 18px;left:134px}

.brand{left:402px;top:30px;width:130px;text-align:center}
.brand-mark{width:30px;height:30px;border-radius:50%;background:#f4c542;margin:0 auto 4px}
.brand-name{font-family:"Roboto",sans-serif;font-weight:700;font-size:8px;line-height:10px;color:#f4d36a;text-transform:uppercase}

.hero{left:0;top:145px;width:927px;height:387px;background:radial-gradient(ellipse at 62% 15%,#fffbe8 0,#dfeaf3 18%,var(--sky-mid) 55%,#5f87ad 100%)}
.hero-caption{left:136px;top:353px;width:379px;height:92px;background:rgba(70,70,70,.72);padding:10px 22px;color:var(--white);font-family:"Roboto",sans-serif;font-weight:700;font-size:24px;line-height:38px;text-transform:uppercase}
.slider-dots{left:137px;top:456px;display:flex;gap:8px}
.slider-dots span{width:13px;height:12px;background:#e4e4e4}
.slider-dots span.on{background:var(--blue-light)}

.notice-bar{left:134px;top:545px;width:663px;height:57px;background:linear-gradient(180deg,#f6f6f6,#e3e3e3);border:1px solid #d0d0d0}
.notice-label{left:0;top:0;width:136px;height:55px;background:var(--blue-light);color:var(--white);font-family:"Roboto",sans-serif;font-size:13.5px;line-height:55px;padding-left:13px;clip-path:polygon(0 0,88% 0,100% 50%,88% 100%,0 100%)}
.notice-title{left:152px;top:11px;font-family:"Roboto",sans-serif;font-weight:500;font-size:11px;color:#222}
.notice-text{left:152px;top:30px;font-size:9.5px;color:#444}
.notice-ref{left:538px;top:30px;font-size:9.5px;color:#444}
.notice-toggle{left:628px;top:17px}

.welcome-title{left:136px;top:617px;font-family:"Roboto",sans-serif;font-size:15.5px;color:#222}
.welcome-text{left:136px;top:648px;width:411px;font-size:8.7px;line-height:19.2px;text-align:justify;color:#333}
.welcome-invite{left:338px;top:725px;font-size:13px;color:var(--blue)}
.motto{left:135px;top:755px;width:412px;height:35px;background:var(--gold);color:var(--white);font-size:14px;line-height:35px;padding-left:16px}
.worship-photo{left:562px;top:614px;width:233px;height:176px;background:linear-gradient(160deg,#d9d6cd,#8a7f75 50%,#3c3634)}

.events{left:135px;top:804px;width:204px;height:216px;border:1px solid #e2e2e2;background:var(--white)}
.events-head{left:0;top:0;width:204px;height:34px;background:linear-gradient(180deg,var(--blue-light),var(--blue));color:var(--white);font-family:"Roboto",sans-serif;font-weight:500;font-size:12.5px;line-height:34px;text-align:center;text-transform:uppercase}
.month-bar{left:0;top:34px;width:204px;height:28px;background:var(--grey-bar);color:var(--white);font-size:11px;line-height:28px;text-align:center}
.month-bar svg{position:absolute;top:6px}
.cal{left:0;top:68px;width:204px;border-collapse:collapse;font-size:7.5px;text-align:center}
.cal th{height:18px;color:#666;font-weight:400;border-bottom:1px solid var(--line)}
.cal td{height:23px;font-weight:600;font-size:8px;color:#444}
.cal td.out{color:#aaa;font-weight:400}
.cal td.mark span{display:inline-block;width:27px;height:22px;line-height:22px;background:#9a9a9a;color:var(--white)}

.donate-box{left:134px;top:1028px;width:206px;height:57px;background:linear-gradient(180deg,#f8f8f8,#dedede);border:1px solid #d4d4d4}
.donate-btn{left:65px;top:8px;width:70px;height:17px;border-radius:9px;background:#f5b63d;font-family:"Roboto",sans-serif;font-weight:700;font-size:10px;line-height:17px;text-align:center;color:#1c3a70}
.cards{left:47px;top:31px;display:flex;gap:3px}
.cards span{width:17px;height:11px;background:#6a7aa0}

.prayer{left:347px;top:800px;width:448px;height:285px;background:linear-gradient(135deg,#fbf6ea,var(--cream))}
.prayer-title{left:19px;top:17px;font-family:"Roboto",sans-serif;font-weight:500;font-size:12.5px;color:#222;text-transform:uppercase}
.prayer-intro{left:19px;top:38px;width:414px;font-size:8.5px;line-height:14.5px;color:#555}
.field{height:24px;background:var(--white);border:1px solid #d6d6d6;font-size:7.8px;color:#555;padding:7px 7px}
.send-btn{left:171px;top:240px;width:89px;height:24px;background:linear-gradient(180deg,var(--blue-light),var(--blue-dark));color:var(--white);font-family:"Roboto",sans-serif;font-size:9.5px;line-height:24px;text-align:center;border-radius:2px}

.footer{left:0;top:1100px;width:927px;height:100px;background:var(--blue);color:var(--white)}
.footer-links{left:136px;top:31px;font-size:9.5px}
.footer-copy{left:136px;top:55px;font-size:8px}
.follow{left:657px;top:27px;font-family:"Roboto",sans-serif;font-size:10.5px}
.social{left:657px;top:47px;display:flex;gap:7px}
.social span{width:22px;height:22px;border-radius:50%;background:rgba(255,255,255,.85)}
</style>
</head>
<body>

<header>
  <div class="abs top-band" role="img" aria-label="Dark cloudy sky banner"></div>
  <div class="abs contact-info">
    <svg width="12" height="18" viewBox="0 0 12 18"><path d="M6 0C2.7 0 0 2.6 0 5.9 0 10 6 18 6 18s6-8 6-12.1C12 2.6 9.3 0 6 0z" fill="#fff"/><circle cx="6" cy="6" r="2.3" fill="#3b4756"/></svg>
    <div>hello@harvestgateway.org<br>48-20 Linden Ave, Queens NY 11420</div>
  </div>
  <div class="abs service-times">
    <svg width="20" height="20" viewBox="0 0 20 20"><circle cx="10" cy="10" r="10" fill="#fff"/><path d="M10 3v3M8.5 4.5h3M5 10l5-3.5 5 3.5v6H5z" stroke="#3b4756" stroke-width="1.3" fill="none"/><rect x="8.7" y="12" width="2.6" height="4" fill="#3b4756"/></svg>
    <div>Sunday Worship: 11:00 am<br>Friday: Prayer 7:30pm</div>
  </div>

  <nav class="abs main-nav">
    <div class="abs nav-item active">Home</div>
    <div class="abs nav-item" style="left:217px">About Us</div>
    <div class="abs nav-item" style="left:301px">Prayer Request</div>
    <div class="abs nav-item" style="left:547px">Events</div>
    <div class="abs nav-item" style="left:628px">Donate</div>
    <div class="abs nav-item" style="left:708px">Contact Us</div>
  </nav>
  <div class="abs brand">
    <div class="brand-mark"></div>
    <div class="brand-name">Harvest Gateway Fellowship Ministries</div>
  </div>
</header>

<section class="abs hero" role="img" aria-label="Bright sky with clouds and a wooden cross"></section>
<div class="abs hero-caption">Open your heart to God!<br>Start a new way of living!</div>
<div class="abs slider-dots"><span></span><span class="on"></span><span></span><span></span><span></span></div>

<section class="abs notice-bar">
  <div class="abs notice-label">NOTIFICATIONS</div>
  <div class="abs notice-title">RANDOM BIBLE VERSE</div>
  <div class="abs notice-text">Now faith is the substance of things hoped for, the evidence of things not seen.</div>
  <div class="abs notice-ref">Hebrews 11:1</div>
  <svg class="abs notice-toggle" width="24" height="28" viewBox="0 0 24 28"><path d="M12 0L24 12H0z" fill="#9a9a9a"/><path d="M0 16H24L12 28z" fill="#9a9a9a"/></svg>
</section>

<section>
  <h1 class="abs welcome-title">WELCOME TO HGFM</h1>
  <p class="abs welcome-text">Welcome to Harvest Gateway Fellowship Ministries, a place where we can come together and fellowship. HGFM is located in Queens, New York and we would love to have you worship with us. We believe God is doing something extraordinary through our church and would like for you to be a part. Please prayerfully consider our church as a place you would like to worship and fellowship with us as we continue to grow.</p>
  <div class="abs welcome-invite">We hope you will visit us real soon</div>
  <div class="abs motto">“ No limits, No Boundaries, but increase in Jesus name ”</div>
  <div class="abs worship-photo" role="img" aria-label="Congregation gathered in worship inside the church hall"></div>
</section>

<section class="abs events">
  <div class="abs events-head">Upcoming Events</div>
  <div class="abs month-bar">
    <svg style="left:8px" width="16" height="16" viewBox="0 0 16 16"><circle cx="8" cy="8" r="7" fill="none" stroke="#fff" stroke-width="1.3"/><path d="M12 8H5M8 5L5 8l3 3" fill="none" stroke="#fff" stroke-width="1.3"/></svg>
    January 2012
    <svg style="right:8px" width="16" height="16" viewBox="0 0 16 16"><circle cx="8" cy="8" r="7" fill="none" stroke="#fff" stroke-width="1.3"/><path d="M4 8h7M8 5l3 3-3 3" fill="none" stroke="#fff" stroke-width="1.3"/></svg>
  </div>
  <table class="abs cal">
    <tr><th>MON</th><th>TUE</th><th>WED</th><th>THU</th><th>FRI</th><th>SAT</th><th>SUN</th></tr>
    <tr><td class="out" style="padding-top:6px">30</td><td style="padding-top:6px">1</td><td style="padding-top:6px">2</td><td style="padding-top:6px">3</td><td style="padding-top:6px">4</td><td style="padding-top:6px">5</td><td style="padding-top:6px">6</td></tr>
    <tr><td>7</td><td>8</td><td>9</td><td>10</td><td>11</td><td>12</td><td>13</td></tr>
    <tr><td>14</td><td>15</td><td>16</td><td>17</td><td>18</td><td>19</td><td>20</td></tr>
    <tr><td>21</td><td>22</td><td class="mark"><span>23</span></td><td>24</td><td class="mark"><span>25</span></td><td>26</td><td>27</td></tr>
    <tr><td>28</td><td>29</td><td>30</td><td>31</td><td class="out">1</td><td class="out">2</td><td class="out">3</td></tr>
  </table>
</section>

<section class="abs donate-box">
  <div class="abs donate-btn">Donate</div>
  <div class="abs cards"><span></span><span></span><span></span><span></span><span></span><span></span></div>
</section>

<section class="abs prayer">
  <h2 class="abs prayer-title">Prayercenter - Submit a prayer request</h2>
  <p class="abs prayer-intro">You are invited to submit your prayer requests below. Your requests will be forwarded to the church. If you wish to send your request privately, submit praise or share a testimony of answered prayers, we will do so. Check the appropriate box below for either of these.</p>
  <div class="abs field" style="left:19px;top:104px;width:193px">Your Name:</div>
  <div class="abs field" style="left:227px;top:104px;width:193px">Your Email</div>
  <div class="abs field" style="left:19px;top:136px;width:193px">Prayer Title:</div>
  <div class="abs field" style="left:227px;top:136px;width:193px">Select a Topic:</div>
  <div class="abs field" style="left:19px;top:166px;width:402px;height:57px">Your Prayer Request:</div>
  <div class="abs send-btn">SEND REQUEST</div>
</section>

<footer class="abs footer">
  <div class="abs footer-links">Privacy Policy | Terms Conditions | Sitemap | Contact Us</div>
  <div class="abs footer-copy">© 2012 HGFM. All Rights Reserved, Contact: 48-20 Linden Ave, Queens NY 11420, (555) 014-2290</div>
  <div class="abs follow">FOLLOW US</div>
  <div class="abs social" aria-label="Social media links"><span></span><span></span><span></span><span></span><span></span></div>
</footer>

</body>
</html>
```